Brightway Haul & Upkeep Services, are a company that offers a 'one stop shop' pre-move clean up a

I have already selected a logo which I would like on the front of the business cards along with phone numbers, web address and email which are:
0487650392
www.brightwayhaul.com.au
brightwayhaulandupkeep@mailbox.example

On the back of the card I would like to list some of the types of service we offer (clean - move - repairs/maintenance) which are:
CLEAN - windows, gutters, solar panels, driveways/paths, carpets.
MOVE - Small/medium size house/office moves, large item pick-up & delivery, yard clean-up and removal.
General maintenance and repairs.

I would like the blue logo on a gray background.

Thanks

```html
<!DOCTYPE html>
<html lang="en">
<head>
<meta charset="utf-8">
<title>Brightway Haul &amp; Upkeep Services – Business Cards</title>
<link rel="stylesheet" href="https://fonts.googleapis.com/css2?family=Open+Sans:wght@400;600;800&family=Quicksand:wght@400;500&display=swap">
<style>
  :root {
    --backdrop: #e9e6e1;
    --card-light: #f4f4f4;
    --card-mid: #d6d6d6;
    --card-dark: #b9b9b9;
    --card-edge: #8e8e8e;
    --brand-blue: #2b6cb4;
    --ink: #2a2a2a;
    --ink-soft: #3c3c3c;
  }
  * { margin: 0; padding: 0; box-sizing: border-box; }
  html, body {
    width: 1200px;
    height: 634px;
    overflow: hidden;
    background: var(--backdrop);
  }
  .sheet {
    position: relative;
    width: 1200px;
    height: 634px;
  }
  .card {
    position: absolute;
    width: 540px;
    height: 312px;
    top: 170px;
  }
  .card--front { left: 40px; }
  .card--back { left: 620px; }
  .card__shape {
    position: absolute;
    inset: 0;
    width: 540px;
    height: 312px;
    filter: drop-shadow(0 6px 10px rgba(0,0,0,0.18));
  }
  .card__content {
    position: absolute;
    inset: 0;
  }
  .brand-name {
    position: absolute;
    font-family: "Open Sans", Arial, sans-serif;
    font-weight: 800;
    color: var(--brand-blue);
    letter-spacing: -0.3px;
    line-height: 1.05;
  }
  .card--front .brand-name {
    left: 44px;
    top: 150px;
    font-size: 31px;
  }
  .card--back .brand-name {
    left: 40px;
    top: 130px;
    font-size: 36px;
  }
  .web-address {
    position: absolute;
    right: 70px;
    top: 96px;
    font-family: "Quicksand", Arial, sans-serif;
    font-size: 13px;
    font-weight: 500;
    color: var(--ink-soft);
  }
  .contact-row {
    position: absolute;
    left: 44px;
    bottom: 30px;
    display: flex;
    gap: 22px;
    font-family: "Quicksand", Arial, sans-serif;
    font-size: 12.5px;
    font-weight: 500;
    color: var(--ink-soft);
  }
  .contact-item {
    display: flex;
    align-items: center;
    gap: 6px;
  }
  .contact-icon {
    width: 12px;
    height: 12px;
    flex: none;
  }
  .service-list {
    position: absolute;
    left: 40px;
    bottom: 44px;
    display: flex;
    gap: 18px;
    list-style: none;
    font-family: "Open Sans", Arial, sans-serif;
    font-size: 17px;
    font-weight: 600;
    color: var(--ink);
  }
  .service-list li::before {
    content: "•";
    color: var(--brand-blue);
    margin-right: 6px;
  }
</style>
</head>
<body>
<main class="sheet">

  <svg width="0" height="0" style="position:absolute" aria-hidden="true">
    <defs>
      <linearGradient id="card-finish" x1="0" y1="0" x2="1" y2="1">
        <stop offset="0" stop-color="var(--card-mid)"/>
        <stop offset="0.4" stop-color="var(--card-light)"/>
        <stop offset="1" stop-color="var(--card-dark)"/>
      </linearGradient>
      <path id="house-card" d="M16,84 H310 L450,12 L486,40 V20 H504 V54 L540,82 V296 Q540,312 524,312 H16 Q0,312 0,296 V100 Q0,84 16,84 Z"/>
    </defs>
  </svg>

  <!-- Front: name and contact details -->
  <section class="card card--front">
    <svg class="card__shape" viewBox="0 0 540 312" aria-hidden="true">
      <use href="#house-card" fill="url(#card-finish)" stroke="var(--card-edge)" stroke-width="1"/>
    </svg>
    <div class="card__content">
      <p class="web-address">www.brightwayhaul.com.au</p>
      <h1 class="brand-name">Brightway Haul<br>&amp; Upkeep Services</h1>
      <div class="contact-row">
        <span class="contact-item">
          <svg class="contact-icon" viewBox="0 0 12 12" aria-hidden="true">
            <circle cx="6" cy="6" r="6" fill="var(--brand-blue)"/>
            <path d="M4.2,3 L5.2,3.2 L5.4,4.6 L4.8,5.1 Q5.6,6.7 6.9,7.3 L7.4,6.7 L8.8,6.9 L9,7.9 Q8.4,9 7.2,8.8 Q4,7.6 3.2,4.6 Q3.1,3.4 4.2,3 Z" fill="#fff"/>
          </svg>
          0487650392
        </span>
        <span class="contact-item">
          <svg class="contact-icon" viewBox="0 0 12 12" aria-hidden="true">
            <circle cx="6" cy="6" r="6" fill="var(--brand-blue)"/>
            <rect x="3" y="4" width="6" height="4.2" fill="#fff"/>
            <path d="M3,4 L6,6.4 L9,4" fill="none" stroke="var(--brand-blue)" stroke-width="0.8"/>
          </svg>
          brightwayhaulandupkeep@mailbox.example
        </span>
      </div>
    </div>
  </section>

  <!-- Back: name and services -->
  <section class="card card--back">
    <svg class="card__shape" viewBox="0 0 540 312" aria-hidden="true">
      <use href="#house-card" fill="url(#card-finish)" stroke="var(--card-edge)" stroke-width="1"/>
    </svg>
    <div class="card__content">
      <h2 class="brand-name">Brightway Haul<br>&amp; Upkeep Services</h2>
      <ul class="service-list">
        <li>Clean</li>
        <li>Move</li>
        <li>General maintenance and repairs.</li>
      </ul>
    </div>
  </section>

</main>
</body>
</html>
```